Heron Loan Partners Business Card

We need a business card design for our mortgage servicing company. In addition to servicing the loans of homeowners, we help homeowners with purchasing their homes and any mortgage refinancing. We would like to see designs that use the colors in the logo attached below (gold-ish yellow and navy blue), and any other design you deem fit! The design should communicate a simpler life with smart mortgages provided by Heron.

```html
<!DOCTYPE html>
<html lang="en">
<head>
<meta charset="utf-8">
<title>Heron Loan Partners Business Card</title>
<link rel="stylesheet" href="https://fonts.googleapis.com/css2?family=Libre+Baskerville:wght@700&family=Poppins:wght@400&display=swap">
<style>
  :root {
    --stage: #b5b5b5;
    --navy: #1f1d58;
    --navy-deep: #251f50;
    --gold: #dfb141;
    --white: #ffffff;
    --rule: #8a87ad;
  }
  html, body { margin: 0; padding: 0; overflow: hidden; }
  body {
    width: 1200px; height: 1200px; background: var(--stage);
    position: relative; font-family: "Poppins", sans-serif;
  }
  .card {
    position: absolute; top: 303px; width: 370px; height: 594px; overflow: hidden;
  }
  .card--front { left: 200px; background: var(--navy); }
  .card--back { left: 599px; width: 364px; background: var(--white); }
  .card svg.shape { position: absolute; inset: 0; }
  .brand-name {
    position: absolute; margin: 0;
    font-family: "Libre Baskerville", serif; font-weight: 700; color: var(--gold);
  }
  .card--front .brand-name { left: 40px; top: 190px; font-size: 58px; }
  .card--back .brand-name { left: 0; right: 0; top: 105px; text-align: center; font-size: 46px; }
  .details {
    position: absolute; left: 0; right: 0; top: 333px; text-align: center; color: var(--white);
  }
  .person-name {
    margin: 0; font-family: "Libre Baskerville", serif; font-weight: 700;
    font-size: 25px; line-height: 30px; color: var(--gold);
  }
  .person-role { margin: 0; font-size: 16px; line-height: 20px; }
  .icon-row {
    display: flex; align-items: center; justify-content: center; gap: 5px; margin-top: 14px;
  }
  .icon-row .rule { width: 50px; height: 1px; background: var(--rule); margin: 0 5px; }
  .icon {
    width: 25px; height: 25px; border-radius: 3px; background: var(--gold);
    display: flex; align-items: center; justify-content: center;
  }
  .contact { margin: 10px 0 0; font-size: 17px; line-height: 21px; }
  .contact p, .address p { margin: 0; }
  .divider { width: 194px; height: 1px; background: var(--rule); margin: 15px auto 13px; }
  .address { font-size: 17px; line-height: 21px; }
</style>
</head>
<body>
  <section class="card card--front">
    <svg class="shape" width="370" height="594" viewBox="0 0 370 594">
      <polygon points="370,125 370,594 60,594" fill="var(--gold)"/>
    </svg>
    <p class="brand-name">Heron</p>
  </section>

  <section class="card card--back">
    <p class="brand-name">Heron</p>
    <svg class="shape" width="364" height="594" viewBox="0 0 364 594">
      <path d="M0 290 C90 290 110 250 190 262 C260 272 300 245 364 236 V594 H0 Z" fill="var(--navy-deep)"/>
      <path d="M0 290 C90 290 110 250 190 262 C260 272 300 245 364 236" fill="none" stroke="var(--gold)" stroke-width="2"/>
    </svg>
    <div class="details">
      <p class="person-name">Daniel Carter</p>
      <p class="person-role">Managing Director</p>
      <div class="icon-row">
        <span class="rule"></span>
        <span class="icon" aria-label="phone">
          <svg width="15" height="13" viewBox="0 0 15 13"><path d="M1 4 Q7.5 -1 14 4 L12 6 L10 4.5 L10 3 Q7.5 2 5 3 L5 4.5 L3 6 Z" fill="#fff"/><rect x="3" y="6.5" width="9" height="5.5" rx="1" fill="#fff"/></svg>
        </span>
        <span class="icon" aria-label="email">
          <svg width="15" height="11" viewBox="0 0 15 11"><rect x="0.5" y="0.5" width="14" height="10" fill="none" stroke="#fff"/><path d="M0.5 0.5 L7.5 6 L14.5 0.5" fill="none" stroke="#fff"/></svg>
        </span>
        <span class="icon" aria-label="website">
          <svg width="15" height="15" viewBox="0 0 15 15"><circle cx="7.5" cy="7.5" r="6.5" fill="#fff"/><circle cx="6" cy="6" r="2.5" fill="var(--gold)"/></svg>
        </span>
        <span class="rule"></span>
      </div>
      <div class="contact">
        <p>044-555 010 234</p>
        <p>info@heronloans.com</p>
        <p>www.heronloans.com</p>
      </div>
      <div class="divider"></div>
      <div class="address">
        <p>421, Address line goes here</p>
        <p>45452,Country Name</p>
      </div>
    </div>
  </section>
</body>
</html>
```